Webdesign für Branchenverzeichnis
Zielgruppe
Wir-bauen-Brücken – das Branchenverzeichnis der Selbstverantwortlichen.
Der Anbieter präsentiert sich mit seinem Namen und der URL - ähnlich wie bei 'blaue Tafeln' oder Jobkranich.
Aufgabenstellung
Das Branchenverzeichnis sollte neutral und gleichzeitig hochwertig sein. Die Hauptfarben sind Gold, Schwarz und Weiß. Logo und Corporate Design wurden bereits entwickelt

```html
<!DOCTYPE html>
<html lang="de">
<head>
<meta charset="utf-8">
<title>Wir-bauen-Brücken – Über uns</title>
<link href="https://fonts.googleapis.com/css2?family=Quicksand:wght@400;500;600;700&display=swap" rel="stylesheet">
<style>
  :root{
    --gold:#d4b26a;
    --ink:#111111;
    --text:#6f6f6f;
    --paper:#fafafa;
    --white:#ffffff;
    --bar-top:#5c5c5c;
    --bar-bottom:#2e2e2e;
    --foot-bottom:#1f1f1f;
    --photo-a:#2a2626;
    --photo-b:#e8c9c0;
  }
  *{box-sizing:border-box;margin:0;padding:0}
  html,body{width:748px;height:1200px;overflow:hidden}
  body{position:relative;background:var(--paper);font-family:'Quicksand',sans-serif;color:var(--text)}
  .abs{position:absolute}

  .site-header{position:absolute;left:0;width:748px;height:39px;background:linear-gradient(var(--bar-top),var(--bar-bottom))}
  .brand{position:absolute;left:97px;top:11px;display:flex;align-items:center;gap:4px}
  .brand-dot{width:16px;height:16px;border:1.2px solid var(--gold);border-radius:50%}
  .brand-name{font-size:6.5px;font-weight:700;color:var(--gold);letter-spacing:.2px;width:34px;line-height:1.15}
  .nav a{position:absolute;top:15px;transform:translateX(-50%);font-size:5.6px;font-weight:700;letter-spacing:.6px;color:var(--white);text-decoration:none;white-space:nowrap}
  .nav a.active{color:var(--gold)}
  .icon-box{position:absolute;top:12px;width:15px;height:15px;border:.8px solid var(--gold);display:flex;align-items:center;justify-content:center}
  .cta{position:absolute;left:573px;top:10px;width:78px;height:18px;background:var(--gold);color:var(--white);font-size:5.2px;font-weight:600;letter-spacing:.4px;display:flex;align-items:center;justify-content:center}

  .title{position:absolute;transform:translateX(-50%);font-size:20px;font-weight:700;letter-spacing:1.4px;color:var(--ink);white-space:nowrap}
  .title span{color:var(--gold)}
  .subtitle{position:absolute;transform:translateX(-50%);font-size:9.8px;font-weight:500;letter-spacing:.4px;color:#333;white-space:nowrap}
  .copy{position:absolute;text-align:center;font-size:6.6px;line-height:12.45px;letter-spacing:.25px;color:var(--text)}
  .copy.lead{color:var(--gold);font-weight:700;font-size:6.9px}
  .photo{position:absolute;background:linear-gradient(135deg,var(--photo-a),#4a3f3e 45%,var(--photo-b))}
  .photo.tall{box-shadow:0 3px 8px rgba(0,0,0,.35)}
  .photo.framed{border:1px solid var(--gold);background:linear-gradient(90deg,#8d8d8f,#c8b2ab 50%,#f1ece9)}
  .quote{position:absolute;font-size:60px;font-weight:700;color:var(--gold);opacity:.25;line-height:1}

  .site-footer{position:absolute;left:0;width:748px;height:118px;background:linear-gradient(var(--bar-top),var(--foot-bottom))}
  .foot-brand{position:absolute;left:165px;top:31px;width:40px;text-align:center}
  .foot-brand .brand-dot{border-color:var(--white);width:18px;height:18px;margin:0 auto 3px}
  .foot-brand .brand-name{color:var(--white);width:40px}
  .foot-col{position:absolute;top:32px}
  .foot-col h4{font-size:7px;font-weight:700;color:var(--white);letter-spacing:.5px;margin-bottom:7px}
  .foot-col p,.foot-col li{font-size:5.8px;color:#e6e6e6;line-height:9.8px;list-style:none}
  .foot-col a{color:#e6e6e6;text-decoration:underline;font-size:5.8px;display:block;margin-top:5px}
  .foot-col ul li{line-height:13px}
  .foot-col ul{margin-top:-2px}
</style>
</head>
<body>

<!-- Variante A -->
<header class="site-header" style="top:0">
  <div class="brand"><span class="brand-dot"></span><span class="brand-name">Wir-bauen-Brücken</span></div>
  <nav class="nav">
    <a style="left:188px">HOME</a><a style="left:239px">SUCHEN</a><a class="active" style="left:297px">ÜBER UNS</a><a style="left:367px">MITGLIEDSCHAFT</a><a style="left:436px">KONTAKT</a>
  </nav>
  <div class="icon-box" style="left:514px"><svg width="11" height="8"><rect width="11" height="2.7" fill="#000"/><rect y="2.7" width="11" height="2.7" fill="#d00"/><rect y="5.4" width="11" height="2.6" fill="#ffce00"/></svg></div>
  <div class="icon-box" style="left:534px"><svg width="8" height="8" viewBox="0 0 8 8"><circle cx="4" cy="2.3" r="1.9" fill="#fff"/><path d="M0.5 8C0.8 5.3 2.2 4.7 4 4.7S7.2 5.3 7.5 8Z" fill="#fff"/></svg></div>
  <div class="cta">MITGLIED WERDEN</div>
</header>

<div class="photo tall" role="img" aria-label="Porträtfoto der Gründerin" style="left:97px;top:78px;width:188px;height:305px"></div>
<h1 class="title" style="left:504px;top:89px">WIR ZEIGEN <span>UNS</span></h1>
<p class="subtitle" style="left:504px;top:116px">Das Branchenverzeichnis der Selbstverantwortlichen</p>
<p class="copy" style="left:372px;top:151px;width:265px">Lorem ipsum dolor sit amet, consectetur adipisicing elit, sed do eiusmod tempor incididunt ut labore et dolore magna aliqua. Duis aute irure dolor in reprehenderit in voluptate velit esse cillum dolore eu fugiat nulla pariatur. Ut enim ad minim veniam, quis nostrud exercitation ullamco laboris nisi ut aliquip ex ea commodo !Lorem ipsum dolor sit amet, consectetur adipisicing elit, sed do eiusmod tempor incididunt ut labore et dolore magna aliqua.</p>
<p class="copy" style="left:372px;top:238px;width:265px">Duis aute irure dolor in reprehenderit in voluptate velit esse cillum dolore eu fugiat nulla pariatur. Ut enim ad minim veniam, quis nostrud exercitation ullamco laboris nisi ut aliquip ex ea commodo!Lorem ipsum dolor sit amet, consectetur adipisicing elit, sed do eiusmod tempor incididunt ut labore et dolore magna aliqua. Duis aute irure dolor in reprehenderit in voluptate velit esse cillum dolore eu fugiat nulla pariatur. Ut enim ad minim veniam, quis nostrud exercitation ullamco laboris nisi ut aliquip ex ea commodo!Lorem ipsum dolor sit amet,</p>
<p class="copy lead" style="left:372px;top:350px;width:265px">Consectetur adipisicing elit, sed do eiusmod tempor incididunt ut labore et dolore magna aliqua. Duis aute irure dolor in reprehenderit.</p>

<footer class="site-footer" style="top:424px">
  <div class="foot-brand"><div class="brand-dot"></div><div class="brand-name">Wir-bauen-Brücken</div></div>
  <div class="foot-col" style="left:224px;width:115px"><h4>WIR BAUEN BRÜCKEN</h4><p>Duis sed odio sit amet nibh vulputate cursus a sit amet mauris Morbi accu.</p><a>Über uns</a></div>
  <div class="foot-col" style="left:404px"><h4>WEBSITE</h4><ul><li>Unternehmen suchen</li><li>Mitgliedschaft</li><li>Kontakt</li></ul></div>
  <div class="foot-col" style="left:523px"><h4>RECHTLICHES</h4><ul><li>Impressum</li><li>Datenschutz</li><li>AGB</li></ul></div>
</footer>

<!-- Variante B -->
<header class="site-header" style="top:669px">
  <div class="brand"><span class="brand-dot"></span><span class="brand-name">Wir-bauen-Brücken</span></div>
  <nav class="nav">
    <a style="left:188px">HOME</a><a style="left:239px">SUCHEN</a><a class="active" style="left:297px">ÜBER UNS</a><a style="left:367px">MITGLIEDSCHAFT</a><a style="left:436px">KONTAKT</a>
  </nav>
  <div class="icon-box" style="left:514px"><svg width="11" height="8"><rect width="11" height="2.7" fill="#000"/><rect y="2.7" width="11" height="2.7" fill="#d00"/><rect y="5.4" width="11" height="2.6" fill="#ffce00"/></svg></div>
  <div class="icon-box" style="left:534px"><svg width="8" height="8" viewBox="0 0 8 8"><circle cx="4" cy="2.3" r="1.9" fill="#fff"/><path d="M0.5 8C0.8 5.3 2.2 4.7 4 4.7S7.2 5.3 7.5 8Z" fill="#fff"/></svg></div>
  <div class="cta">MITGLIED WERDEN</div>
</header>

<h1 class="title" style="left:374px;top:742px">WIR ZEIGEN <span>UNS</span></h1>
<p class="subtitle" style="left:374px;top:769px">Das Branchenverzeichnis der Selbstverantwortlichen</p>
<div class="photo framed" role="img" aria-label="Porträtfoto der Gründerin" style="left:136px;top:812px;width:156px;height:109px"></div>
<p class="copy" style="left:324px;top:828px;width:267px">Lorem ipsum dolor sit amet, consectetur adipisicing elit, sed do eiusmod tempor incididunt ut labore et dolore magna aliqua. Duis aute irure dolor in reprehenderit in voluptate velit esse cillum dolore eu fugiat nulla pariatur. Ut enim ad minim veniam, quis nostrud exercitation ullamco laboris nisi ut aliquip ex ea commodo !Lorem ipsum dolor sit amet, consectetur adipisicing elit, sed do eiusmod tempor incididunt ut labore et dolore magna aliqua.</p>
<div class="quote" style="left:434px;top:886px">”</div>
<p class="copy" style="left:138px;top:943px;width:453px">Duis aute irure dolor in reprehenderit in voluptate velit esse cillum dolore eu fugiat nulla pariatur. Ut enim ad minim veniam, quis nostrud exercitation ullamco laboris nisi ut aliquip ex ea commodo!Lorem ipsum dolor sit amet, consectetur adipisicing elit, sed do eiusmod tempor incididunt ut labore et dolore magna aliqua. Duis aute irure dolor in reprehenderit in voluptate velit esse cillum dolore eu fugiat nulla pariatur. Ut enim ad minim veniam, quis nostrud exercitation ullamco laboris nisi ut aliquip ex ea commodo! Lorem ipsum dolor sit amet,</p>
<p class="copy lead" style="left:138px;top:1018px;width:453px">Consectetur adipisicing elit, sed do eiusmod tempor incididunt ut labore et dolore magna aliqua. Duis aute irure dolor in reprehenderit smod tempor incididunt ut labore et dolore magna aliqua. Duis aute irure dolor in reprehenderit.</p>

<footer class="site-footer" style="top:1082px">
  <div class="foot-brand"><div class="brand-dot"></div><div class="brand-name">Wir-bauen-Brücken</div></div>
  <div class="foot-col" style="left:224px;width:115px"><h4>WIR BAUEN BRÜCKEN</h4><p>Duis sed odio sit amet nibh vulputate cursus a sit amet mauris Morbi accu.</p><a>Über uns</a></div>
  <div class="foot-col" style="left:404px"><h4>WEBSITE</h4><ul><li>Unternehmen suchen</li><li>Mitgliedschaft</li><li>Kontakt</li></ul></div>
  <div class="foot-col" style="left:523px"><h4>RECHTLICHES</h4><ul><li>Impressum</li><li>Datenschutz</li><li>AGB</li></ul></div>
</footer>

</body>
</html>
```